Make my current Presentation more Professional

I am selling frozen pulp and sorbets. I have a presentation done to introduce the product to customers i want to sell my product to. However the presentation does not have a character - i need to make it look more professional, and at the same time i want to make the product stand out, and have the overall presentation look very fresh, and embedding the true look and feel of what we are offering. 100% NATURAL TROPICAL BRAZILIAN FRUITS.
Some of the text in the presentation is pasted like image, i need it as text.
There should be a specific template that you will use so that i can add remove slides later on according to my requirement

Target Market(s)

Presentation is intended for F&B managers & Chefs in hotels, restaurant

Industry/Entity Type

Food Service

Font styles to use
Sans Serif

Colors

Designer to choose colors to be used in the design.

Requirements
Must have
• A fresh, natural look and feel of tropical fruits.
• It also should come across professional as we are selling products to potential customers.
• I need a clear template - with header, font etc..
Nice to have
• If you want to buy some pictures of fruits, i can buy it for you to make it look great

```html
<!DOCTYPE html>
<html lang="en">
<head>
<meta charset="utf-8">
<title>Our Vision</title>
<link rel="stylesheet" href="https://fonts.googleapis.com/css2?family=Bitter:wght@600&family=Asap:wght@400;600&display=swap">
<style>
  :root {
    --bg-light: #f4f4f4;
    --bg-shade: #e9e9e8;
    --accent-green: #8cc131;
    --brand-green: #2f8a2b;
    --text-dark: #3a3a3a;
    --photo-warm: #e8a062;
    --photo-deep: #b23a4a;
  }
  * { margin: 0; padding: 0; box-sizing: border-box; }
  html, body { width: 1200px; height: 675px; overflow: hidden; }
  body { background: var(--bg-light); }
  .slide {
    position: relative;
    width: 1200px;
    height: 675px;
    overflow: hidden;
    background: radial-gradient(ellipse at 75% 35%, #f7f7f7 0%, var(--bg-light) 55%, var(--bg-shade) 100%);
  }
  .photo-area {
    position: absolute;
    left: 0;
    top: 0;
    width: 535px;
    height: 675px;
    background: linear-gradient(100deg, var(--photo-warm) 0%, #d9804f 60%, var(--photo-deep) 100%);
  }
  .vision {
    position: absolute;
    left: 643px;
    top: 136px;
    width: 520px;
  }
  .vision-title {
    font-family: "Bitter", Georgia, serif;
    font-weight: 600;
    font-size: 41px;
    line-height: 1.2;
    color: var(--accent-green);
    margin-bottom: 24px;
  }
  .vision-text {
    font-family: "Asap", Arial, sans-serif;
    font-weight: 400;
    font-size: 22.5px;
    line-height: 45px;
    color: var(--text-dark);
    white-space: nowrap;
  }
  .vision-text strong { font-weight: 600; }
  .brand {
    position: absolute;
    left: 1020px;
    top: 604px;
    display: flex;
    align-items: center;
    gap: 7px;
  }
  .brand-dot {
    width: 26px;
    height: 26px;
    border-radius: 50%;
    background: var(--brand-green);
  }
  .brand-name {
    font-family: "Asap", Arial, sans-serif;
    font-weight: 600;
    font-size: 21px;
    color: var(--brand-green);
  }
</style>
</head>
<body>
  <main class="slide">
    <div class="photo-area" role="img" aria-label="Close-up photograph of a halved passion fruit showing orange seed pulp inside a red rind"></div>

    <section class="vision">
      <h1 class="vision-title">Our Vision</h1>
      <p class="vision-text">To become the <strong>number one company</strong><br>providing <strong>high quality exotic fruit pulps,</strong><br><strong>vitaminas sorbetti &amp; gelato.</strong></p>
    </section>

    <div class="brand">
      <span class="brand-dot"></span>
      <span class="brand-name">Polpa Viva</span>
    </div>
  </main>
</body>
</html>
```